Business Cards Design for the electrical wholesaler: clean bold dynamic :)

We need a business card design that would follow our latest brand guidelines. As an electrical wholesaler we want to bring a fresh look and feel into the industry. The design should be clean bold and dynamic. It should come alive with the renewed energy of our green colour. Our grey colour should keep things balanced and complement the notion of maturity and responsibility. We employ Lato as a corporate font however are not bound by this font and we’re open to interpretation here.

Target Market(s)

Electrical contractors

Industry/Entity Type

Business

Contact Information for Business Card

Logo
Name & Surname: Halyna Dorosh
Job Title: Director of Marketing
Email: halya.dorosh@quillmail.example
Cell phone: XXX.XXX.XXXX
Address: 20517 - 87 Ave. Edmonton, AB, Canada. T6K 4N8
Business Phone: 780.555.0184
Website: www.brovix.example

Font styles to use
Other font styles liked:
• Lato

Requirements
Must have
• Logo & website
Nice to have
• Brand elements - some of them you may find in the attached Brand Guidelines (e.g. three lines on the background signifying "W")

```html
<!DOCTYPE html>
<html lang="en">
<head>
<meta charset="utf-8">
<title>brovix business card</title>
<link href="https://fonts.googleapis.com/css2?family=Lato:wght@400;700;900&display=swap" rel="stylesheet">
<style>
  :root {
    --backdrop: #3b3b3c;
    --card: #2a2a2b;
    --gloss: #1c1c1d;
    --ink-soft: #4a4a4c;
    --grey: #a7a7a7;
    --white: #f2f2f2;
    --green: #7dc423;
  }
  * { margin: 0; padding: 0; box-sizing: border-box; }
  html, body { width: 799px; height: 1200px; overflow: hidden; }
  body {
    background: var(--backdrop);
    font-family: "Lato", sans-serif;
    position: relative;
  }
  .card {
    position: absolute;
    left: 105px;
    width: 588px;
    height: 336px;
    border-radius: 22px;
    background: var(--card);
    overflow: hidden;
    box-shadow: 0 14px 30px rgba(0,0,0,.35);
  }
  .card--front { top: 130px; }
  .card--back { top: 730px; }

  /* front */
  .front-brand {
    position: absolute;
    left: 150px;
    top: 110px;
    display: flex;
    align-items: center;
    gap: 16px;
  }
  .front-brand .brand-square {
    width: 46px; height: 46px;
    background: var(--gloss);
    border-radius: 4px;
  }
  .front-brand .brand-name {
    font-size: 76px;
    font-weight: 700;
    line-height: 1;
    color: var(--gloss);
    letter-spacing: 1px;
  }
  .front-tagline {
    position: absolute;
    left: 212px;
    top: 196px;
    font-size: 15px;
    letter-spacing: 3px;
    color: var(--ink-soft);
    text-transform: uppercase;
  }

  /* back */
  .back-brand {
    position: absolute;
    left: 30px;
    top: 26px;
    display: flex;
    align-items: center;
    gap: 10px;
  }
  .back-brand .brand-square {
    width: 30px; height: 30px;
    background: var(--grey);
    border-radius: 3px;
  }
  .back-brand .brand-name {
    font-size: 42px;
    font-weight: 700;
    line-height: 1;
    color: var(--white);
  }
  .back-tagline {
    position: absolute;
    left: 72px;
    top: 74px;
    font-size: 9px;
    letter-spacing: 1.6px;
    color: var(--green);
    text-transform: uppercase;
  }
  .person { position: absolute; left: 30px; top: 102px; }
  .person-name {
    font-size: 27px;
    font-weight: 700;
    color: var(--green);
    line-height: 1.1;
  }
  .person-title {
    font-size: 15px;
    color: var(--white);
    margin-top: 2px;
  }
  .address {
    position: absolute;
    left: 30px;
    top: 170px;
    font-size: 15px;
    line-height: 1.3;
    color: var(--white);
    font-style: normal;
  }
  .contacts {
    position: absolute;
    left: 30px;
    top: 222px;
    list-style: none;
    font-size: 15px;
    color: var(--white);
  }
  .contacts li {
    display: flex;
    align-items: center;
    gap: 10px;
    line-height: 23px;
  }
  .contacts svg { width: 14px; height: 14px; flex: none; }
  .accent-band {
    position: absolute;
    right: 0;
    top: 0;
    width: 150px;
    height: 336px;
  }
</style>
</head>
<body>

<section class="card card--front" aria-label="Card front">
  <div class="front-brand">
    <span class="brand-square"></span>
    <span class="brand-name">brovix</span>
  </div>
  <p class="front-tagline">Electrical Wholesalers</p>
</section>

<section class="card card--back" aria-label="Card back">
  <div class="back-brand">
    <span class="brand-square"></span>
    <span class="brand-name">brovix</span>
  </div>
  <p class="back-tagline">Electrical Wholesalers</p>

  <div class="person">
    <p class="person-name">Halyna Dorosh</p>
    <p class="person-title">Founder &amp; CEO</p>
  </div>

  <address class="address">
    20517 - 87 Ave. Edmonton,<br>
    AB, Canada T6K 4N8
  </address>

  <ul class="contacts">
    <li>
      <svg viewBox="0 0 14 14" aria-hidden="true"><circle cx="7" cy="7" r="7" fill="var(--green)"/><path d="M4.5 3.5l1.6 0 .6 1.8-1 .8a5 5 0 0 0 2.2 2.2l.8-1 1.8.6v1.6c-3.6.3-6.3-2.4-6-6z" fill="var(--card)"/></svg>
      +1 780-555-0184
    </li>
    <li>
      <svg viewBox="0 0 14 14" aria-hidden="true"><circle cx="7" cy="7" r="7" fill="var(--green)"/><rect x="3.5" y="4.5" width="7" height="5" fill="var(--card)"/><path d="M3.5 4.5l3.5 2.8 3.5-2.8" fill="none" stroke="var(--green)" stroke-width=".8"/></svg>
      hello@brovix.example
    </li>
    <li>
      <svg viewBox="0 0 14 14" aria-hidden="true"><circle cx="7" cy="7" r="7" fill="var(--green)"/><circle cx="7" cy="7" r="3.6" fill="none" stroke="var(--card)" stroke-width="1"/><path d="M3.4 7h7.2M7 3.4c-1.6 2.2-1.6 5 0 7.2M7 3.4c1.6 2.2 1.6 5 0 7.2" fill="none" stroke="var(--card)" stroke-width=".8"/></svg>
      www.brovix.example
    </li>
  </ul>

  <svg class="accent-band" viewBox="0 0 150 336" preserveAspectRatio="none" aria-hidden="true">
    <path d="M90 0 H150 V336 H70 C98 250 112 120 90 0 Z" fill="var(--green)"/>
  </svg>
</section>

</body>
</html>
```